Social Media Graphics - Oakline Push REVISED

Create 6-7 individual social media graphics (square size) to encourage folks to join our online course called:

The Harvest Ledger Circle
How to Launch a Multi-Million Business From Scratch
Sign Up Today!

IMPORTANT: Make the largest and most prominent text on the graphic be: How to Launch a Multi-Million Business From Scratch

For the color scheme of the graphics, let's try a blue color palette; make sure the graphics appeal to both men and women

Make sure each graphic contains 1 of the 3 pics attached (crop pic as needed); and make sure one of the graphics is all TEXT only.

Target Market(s)

men and women looking to start a business

Industry/Entity Type

Entrepreneurship

Colors
0054AA
0677BA
7BADD7
CADEEF
E8F1F8

Requirements
Must have
• All the text and use the 3 pics provided; one graphic can be all text; Simple, modern design that's easy to read

```html
<!DOCTYPE html>
<html lang="en">
<head>
<meta charset="utf-8">
<title>The Harvest Ledger Circle – Sign Up</title>
<link rel="stylesheet" href="https://fonts.googleapis.com/css2?family=Exo+2:ital,wght@1,700;1,800;1,900&display=swap">
<style>
  :root {
    --sky: #0779BC;
    --royal: #0054AA;
    --ice: #E8F1F8;
    --mist: #CADEEF;
    --steel: #7BADD7;
    --white: #FFFFFF;
    --snow: #F1F3F6;
    --cyan: #1BA6E6;
    --cyan-light: #5FD3FF;
    --navy: #0B2A7A;
  }
  * { margin: 0; padding: 0; box-sizing: border-box; }
  html, body { width: 1200px; height: 1200px; overflow: hidden; }
  body {
    background: var(--sky);
    font-family: "Exo 2", "Arial Black", sans-serif;
    position: relative;
  }
  .promo-panel {
    position: absolute;
    left: 36px; top: 237px;
    width: 1128px; height: 593px;
    background: var(--royal);
    border-radius: 84px;
  }
  .course-title {
    position: absolute;
    left: 0; right: 0; top: 284px;
    display: flex; justify-content: center; align-items: center; gap: 16px;
    font-style: italic;
    font-weight: 900;
    text-transform: uppercase;
    white-space: nowrap;
  }
  .title-word {
    color: var(--white);
    font-size: 58px;
    line-height: 1;
    letter-spacing: -0.5px;
  }
  .title-pill {
    height: 82px;
    padding: 0 22px;
    display: flex; align-items: center;
    background: linear-gradient(180deg, var(--ice) 0%, var(--mist) 100%);
    border: 2px solid var(--navy);
    border-radius: 14px;
    color: var(--royal);
    font-size: 52px;
    line-height: 1;
    letter-spacing: -0.5px;
  }
  .course-tagline {
    position: absolute;
    left: 60px; right: 60px; top: 412px;
    display: flex; flex-direction: column; align-items: center;
    color: var(--snow);
    font-style: italic;
    font-weight: 900;
    font-size: 80px;
    line-height: 88px;
    letter-spacing: -1px;
    text-transform: uppercase;
    text-align: center;
  }
  .course-tagline span { white-space: nowrap; }
  .signup-button {
    position: absolute;
    left: 337px; top: 795px;
    width: 525px; height: 106px;
    border-radius: 53px;
    background: var(--navy);
    padding: 7px;
  }
  .signup-button span {
    display: flex; align-items: center; justify-content: center;
    width: 100%; height: 100%;
    border-radius: 46px;
    background: linear-gradient(180deg, var(--cyan-light) 0%, var(--cyan) 55%, #0C8BD0 100%);
    box-shadow: inset 0 0 0 4px rgba(255,255,255,0.35);
    color: var(--white);
    font-style: italic;
    font-weight: 900;
    font-size: 50px;
    text-transform: uppercase;
    text-shadow: 0 2px 3px rgba(11,42,122,0.6);
  }
</style>
</head>
<body>
  <div class="promo-panel"></div>

  <p class="course-title">
    <span class="title-word">The</span>
    <span class="title-pill">Harvest Ledger</span>
    <span class="title-word">Circle</span>
  </p>

  <h1 class="course-tagline">
    <span>How to launch a</span>
    <span>multi-million business</span>
    <span>from scratch</span>
  </h1>

  <div class="signup-button"><span>Sign up today!</span></div>
</body>
</html>
```